Redesign Canvas Art E-Commerce Website

Help! I hired a couple of companies on Brisklo.com to build and design an e-commerce website for me. After three long and painful months, I have one that I believe is functional on the back-end, but aesthetically on the front end is a mess.

We are a small family business that will take your digital photo and manipulate it into a digitally created oil, watercolor or impressionist style pieces of artwork that we print on museum quality, gallery grade canvas and ship to the customer, ready to hang.

We are looking to create an e-commerce website where a customer can choose their art style, upload a photo, choose their canvas size and orientation (horizontal or vertical) and checkout. Within 48 hours, we will send them back a proof of their newly created, customized artwork for them to approve or not approve. If they approve, we print, package and ship them the product. If they do not approve, we offer unlimited revisions until they are happy.

As I mentioned, the back end functionality is already there, just need design help. No coding required

Here is a link to the development page that they created: https://plumwickstudio.com/development/

As you can see, it looks off...doesnt line up properly, wasted space, weird font. Feel free to either correct the homepage they created or design an entirely new page. I am attaching some examples of before and after photos of artwork for reference. I also think the testimonials page and shop page can use a little style. The content is there and accurate, it just doesn't look pretty. Please keep in mind that our customers will probably not be very tech savvy. The customers will probably be sending us pics of kids, grandkids, pets, family portraits, vacation photos, etc.

Here is one of our competitors - www.gildavantry.com
Their website looks clean and inviting.

Thank you in advance! Im looking forward to seeing the results. I am including our logo in the attachments (I do not have it in a vector file, just a jpeg)

Target Market(s)

Non tech-savvy indiduals, 30-70 years old

Industry/Entity Type

Please look at https://plumwickstudio.com/development/ to see various pages and what the other designers did

Number of Pages Required

1 page

Requirements
Must have
• Verbiage on pages leave "as is" but feel free to change styles. Would like to keep existing four categories on homepage
Nice to have
• Warm and inviting homepage that evokes emotion

```html
<!DOCTYPE html>
<html lang="en">
<head>
<meta charset="utf-8">
<title>Plumwick Studio — Turn Your Digital Photos Into Wall Art</title>
<link href="https://fonts.googleapis.com/css2?family=Mulish:wght@400;600;700;800;900&family=Nunito:wght@800;900&display=swap" rel="stylesheet">
<style>
:root{
  --accent:#e8542a;
  --ink:#1a1a1a;
  --text:#444;
  --muted:#777;
  --soft:#f4f3f3;
  --line:#d6d6d6;
  --black:#0b0b0b;
  --white:#fff;
}
*{box-sizing:border-box;margin:0;padding:0}
html,body{width:1200px;height:3950px;overflow:hidden}
body{position:relative;background:var(--white);font-family:'Mulish',sans-serif;color:var(--text)}
.abs{position:absolute}
.btn{position:absolute;background:var(--accent);color:var(--white);font-weight:800;font-size:14px;letter-spacing:.3px;display:flex;align-items:center;justify-content:center;text-transform:uppercase}
.section-title{position:absolute;left:0;width:1200px;text-align:center;font-weight:800;font-size:26px;color:var(--ink);letter-spacing:.3px}
.title-rule{position:absolute;left:584px;width:32px;height:3px;background:var(--accent)}

/* top bar */
.topbar{left:0;top:0;width:1200px;height:34px;background:var(--black);color:var(--white);font-size:12.5px;font-weight:600;display:flex;align-items:center;justify-content:center;letter-spacing:.2px}

/* header */
.brand{position:absolute;display:flex;align-items:center;gap:10px;font-weight:800;color:var(--ink)}
.brand-dot{width:14px;height:14px;border-radius:50%;background:var(--accent)}
.header-brand{left:133px;top:63px;font-size:26px}
.nav{position:absolute;top:70px;left:409px;display:flex;gap:0;font-size:15px;color:var(--ink)}
.nav a{position:absolute;white-space:nowrap;color:var(--ink);text-decoration:none}
.nav a.active{color:var(--accent);text-decoration:underline}
.cart{left:1030px;top:66px}
.cart-badge{position:absolute;left:1052px;top:67px;width:15px;height:15px;border-radius:50%;background:var(--accent);color:var(--white);font-size:10px;display:flex;align-items:center;justify-content:center;font-weight:700}

/* hero */
.hero{left:133px;top:130px;width:935px;height:537px;background:linear-gradient(120deg,#3f5a23 0%,#6b3a24 40%,#e9e2d6 55%,#2f4a1d 80%,#7a5a2f 100%)}
.hero-title{position:absolute;left:192px;top:216px;font-family:'Nunito',sans-serif;font-weight:900;font-size:42px;line-height:44px;color:var(--white)}
.hero-btn{left:196px;top:420px;width:172px;height:48px;font-size:14.5px}
.dots{position:absolute;left:566px;top:627px;display:flex;gap:10px}
.dots span{width:10px;height:10px;border-radius:50%;background:var(--white)}
.dots span.on{background:var(--accent)}

/* categories */
.cat-img{position:absolute;width:446px;height:313px}
.cat-name{position:absolute;font-weight:700;font-size:19px;color:var(--ink)}
.cat-rule{position:absolute;width:298px;border-bottom:1.5px dotted #888}
.cat-btn{width:133px;height:37px;font-size:14px}

/* about */
.about-band{left:0;top:1631px;width:1200px;height:472px;background:var(--soft)}
.about-img{left:132px;top:1688px;width:438px;height:354px;background:radial-gradient(circle at 55% 40%,#c58a5c 0%,#7a3d1f 45%,#2b1a12 100%)}
.about-title{left:619px;top:1681px;font-weight:800;font-size:26px;color:var(--ink)}
.about-rule{left:619px;top:1724px;width:34px;height:3px;background:var(--accent)}
.about-text{left:619px;top:1752px;width:440px;font-size:13.6px;line-height:22.5px;color:#333}
.about-text p+p{margin-top:18px}
.about-btn{left:619px;top:1999px;width:134px;height:35px;font-size:14px}

/* best sellers */
.product-img{position:absolute;top:2243px;width:221px;height:296px}
.product-name{position:absolute;top:2558px;font-weight:700;font-size:17px;color:var(--ink)}
.product-price{position:absolute;top:2583px;font-weight:800;font-size:17px;color:var(--ink)}
.product-price s{font-weight:400;font-size:11px;color:var(--muted);margin-left:6px}
.arrow{position:absolute}
.view-btn{left:549px;top:2647px;width:103px;height:36px;font-size:14px}

/* testimonials */
.testi-band{left:0;top:2736px;width:1200px;height:526px;background:var(--soft)}
.testi-card{position:absolute;top:2863px;width:299px;height:344px;background:var(--soft);border:1px solid var(--line);text-align:center}
.quote{margin-top:28px;font-family:'Nunito',sans-serif;font-weight:900;font-size:50px;line-height:40px;color:var(--accent);height:36px}
.stars{margin-top:6px;color:#f0a21b;font-size:13px;letter-spacing:2px}
.testi-text{margin:12px auto 0;width:246px;font-size:12.2px;line-height:19.5px;color:#555}
.testi-rule{width:22px;height:1px;background:var(--accent);margin:20px auto 0}
.testi-name{margin-top:14px;font-weight:800;font-size:12.5px;color:var(--ink)}
.testi-place{margin-top:2px;font-size:12.5px;color:#555}

/* why us */
.why-deco{position:absolute;top:3395px;width:158px;height:138px;border-radius:50%;background:radial-gradient(circle at 35% 50%,rgba(240,140,40,.55),rgba(90,170,220,.25) 55%,rgba(255,255,255,0) 72%)}
.why-circle{position:absolute;top:3407px;width:114px;height:114px;border-radius:50%;background:#f2f2f2;display:flex;align-items:center;justify-content:center}
.why-title{position:absolute;top:3555px;width:300px;text-align:center;font-weight:700;font-size:17.5px;color:var(--ink)}
.why-text{position:absolute;top:3594px;width:240px;text-align:center;font-size:12.5px;line-height:19px;color:#555}

/* footer */
.footer{left:0;top:3730px;width:1200px;height:220px;background:var(--black);color:var(--white)}
.footer-brand{left:133px;top:3783px;font-size:30px;color:var(--white)}
.footer-email{left:711px;top:3760px;font-size:13.5px;line-height:21px}
.follow{left:946px;top:3752px;font-size:13.5px}
.social{position:absolute;top:3776px;width:24px;height:24px;border-radius:50%}
.footer-links{position:absolute;left:380px;top:3824px;width:688px;display:flex;justify-content:space-between;font-size:12.5px;color:#ddd}
.footer-links .sep{color:#888}
.footer-rule{left:133px;top:3871px;width:935px;height:1px;background:#333}
.copyright{left:0;top:3902px;width:1200px;text-align:center;font-size:11px;color:#ddd}
</style>
</head>
<body>

<div class="abs topbar">FREE SHIPPING FOR ALL USA &nbsp;ORDERS</div>

<header>
  <div class="brand header-brand"><span class="brand-dot"></span>Plumwick Studio</div>
  <nav class="nav">
    <a class="active" style="left:0">Home</a>
    <a style="left:76px">Shop</a>
    <a style="left:141px">Testimonials</a>
    <a style="left:256px">About Us</a>
    <a style="left:350px">FAQs</a>
    <a style="left:421px">My Orders</a>
    <a style="left:525px">Contact Us</a>
  </nav>
  <svg class="abs cart" width="28" height="26" viewBox="0 0 28 26" fill="none" stroke="#1a1a1a" stroke-width="2">
    <path d="M1 3h4l3 14h14l3-10H7"/><circle cx="10" cy="22" r="2"/><circle cx="20" cy="22" r="2"/>
  </svg>
  <div class="cart-badge">0</div>
</header>

<section>
  <div class="abs hero" role="img" aria-label="Oil painting style photo of a bride and groom embracing with a bouquet in front of green foliage"></div>
  <h1 class="hero-title">Turn Your Digital<br>Photos Into<br>One of a Kind<br>Wall Art</h1>
  <div class="btn hero-btn">Get Started</div>
  <div class="dots"><span></span><span class="on"></span><span></span><span></span></div>
</section>

<section>
  <h2 class="section-title" style="top:709px">CATEGORIES</h2>
  <div class="title-rule" style="top:753px"></div>

  <div class="cat-img" style="left:132px;top:794px;background:linear-gradient(135deg,#e9e6e2,#a8683a 45%,#e0913f 70%,#f1eeea)" role="img" aria-label="Oil style painting of a dog resting with an orange cat"></div>
  <div class="cat-name" style="left:132px;top:1127px">Oil</div>
  <div class="cat-rule" style="left:132px;top:1162px"></div>
  <div class="btn cat-btn" style="left:445px;top:1127px">Get Started</div>

  <div class="cat-img" style="left:619px;top:794px;background:linear-gradient(135deg,#d9c6b6,#f0e6de 45%,#ffffff 100%)" role="img" aria-label="Watercolor style portrait of a mother holding her baby close"></div>
  <div class="cat-name" style="left:619px;top:1127px">Watercolor</div>
  <div class="cat-rule" style="left:619px;top:1162px"></div>
  <div class="btn cat-btn" style="left:933px;top:1127px">Get Started</div>

  <div class="cat-img" style="left:132px;top:1200px;background:linear-gradient(135deg,#8fb07a,#c9d9d6 45%,#7ab0cc 70%,#4f6b3a)" role="img" aria-label="Impressionist style painting of a smiling older couple, piggyback ride outdoors"></div>
  <div class="cat-name" style="left:130px;top:1532px">Impressionist</div>
  <div class="cat-rule" style="left:132px;top:1567px"></div>
  <div class="btn cat-btn" style="left:445px;top:1533px">Get Started</div>

  <div class="cat-img" style="left:619px;top:1200px;background:linear-gradient(160deg,#5e6b3a,#b9b08a 45%,#8a7f6a 75%,#4d5530)" role="img" aria-label="Photo of a father and child walking hand in hand along a forest path"></div>
  <div class="cat-name" style="left:619px;top:1532px">Digital Photo</div>
  <div class="cat-rule" style="left:619px;top:1567px"></div>
  <div class="btn cat-btn" style="left:933px;top:1533px">Get Started</div>
</section>

<section>
  <div class="abs about-band"></div>
  <div class="abs about-img" role="img" aria-label="Oil painting style portrait of a smiling bride with white flowers"></div>
  <h2 class="abs about-title">ABOUT US</h2>
  <div class="abs about-rule"></div>
  <div class="abs about-text">
    <p>At Plumwick Studio, we take your digital photo and turn it<br>into a one-of-a-kind piece of artwork!</p>
    <p>The process couldn’t be any easier. Simply upload your photo, choose your art style and size, and let our team of skilled digital artists do the rest. Do you want to put your digital photo on canvas without an art style? No problem! Just choose the “Digital Photo/Retouching” category and upload your photo. We can print your photo “as is” or do some minor retouching (e.g. remove objects, enhance colors, lighten photo, etc)</p>
  </div>
  <div class="btn about-btn">Read More</div>
</section>

<section>
  <h2 class="section-title" style="top:2150px">BEST SELLERS</h2>
  <div class="title-rule" style="top:2197px"></div>

  <svg class="arrow" style="left:66px;top:2377px" width="16" height="28" viewBox="0 0 16 28" fill="none" stroke="#999" stroke-width="3"><path d="M14 2L3 14l11 12"/></svg>
  <svg class="arrow" style="left:1105px;top:2377px" width="16" height="28" viewBox="0 0 16 28" fill="none" stroke="#999" stroke-width="3"><path d="M2 2l11 12L2 26"/></svg>

  <div class="product-img" style="left:130px;background:linear-gradient(160deg,#3f5a23,#d9d2c4 50%,#2a2f3a 85%)" role="img" aria-label="Painted bride and groom on canvas"></div>
  <div class="product-name" style="left:130px">Lorem Ipsum</div>
  <div class="product-price" style="left:130px">$59.95<s>$75.95</s></div>

  <div class="product-img" style="left:369px;background:linear-gradient(160deg,#5aa6dc,#8a4a22 45%,#5b2d14 65%,#9fd0ef)" role="img" aria-label="Painted horse and rider jumping"></div>
  <div class="product-name" style="left:369px">Lorem Ipsum</div>
  <div class="product-price" style="left:369px">$59.95<s>$75.95</s></div>

  <div class="product-img" style="left:608px;background:linear-gradient(160deg,#6b8a3a,#d8d4cc 45%,#4a4a4a 70%,#a88a5a)" role="img" aria-label="Painted fluffy puppy"></div>
  <div class="product-name" style="left:608px">Lorem Ipsum</div>
  <div class="product-price" style="left:608px">$59.95<s>$75.95</s></div>

  <div class="product-img" style="left:846px;background:linear-gradient(160deg,#eef0ea,#9ab088 45%,#7ab0cc 75%,#eef0ea)" role="img" aria-label="Painted older couple laughing"></div>
  <div class="product-name" style="left:846px">Lorem Ipsum</div>
  <div class="product-price" style="left:846px">$59.95<s>$75.95</s></div>

  <div class="btn view-btn">View All</div>
</section>

<section>
  <div class="abs testi-band"></div>
  <h2 class="section-title" style="top:2771px">TESTIMONIALS</h2>
  <div class="title-rule" style="top:2819px"></div>

  <svg class="arrow" style="left:66px;top:3023px" width="16" height="28" viewBox="0 0 16 28" fill="none" stroke="#999" stroke-width="3"><path d="M14 2L3 14l11 12"/></svg>
  <svg class="arrow" style="left:1105px;top:3023px" width="16" height="28" viewBox="0 0 16 28" fill="none" stroke="#999" stroke-width="3"><path d="M2 2l11 12L2 26"/></svg>

  <div class="testi-card" style="left:133px">
    <div class="quote">“</div>
    <div class="stars">★★★★★</div>
    <p class="testi-text">My mom is in an assisted living facility and has Alzheimers. We had a family portrait made into an oil and put in her room to help her remember us. The nurses always tell us how much she loves it and helps jog her memory. Thank you Plumwick Studio!</p>
    <div class="testi-rule"></div>
    <div class="testi-name">Marla T</div>
    <div class="testi-place">Fairview, MD</div>
  </div>
  <div class="testi-card" style="left:449px">
    <div class="quote">“</div>
    <div class="stars">★★★★★</div>
    <p class="testi-text">My mom is in an assisted living facility and has Alzheimers. We had a family portrait made into an oil and put in her room to help her remember us. The nurses always tell us how much she loves it and helps jog her memory. Thank you Plumwick Studio!</p>
    <div class="testi-rule"></div>
    <div class="testi-name">Marla T</div>
    <div class="testi-place">Fairview, MD</div>
  </div>
  <div class="testi-card" style="left:766px">
    <div class="quote">“</div>
    <div class="stars">★★★★★</div>
    <p class="testi-text">My mom is in an assisted living facility and has Alzheimers. We had a family portrait made into an oil and put in her room to help her remember us. The nurses always tell us how much she loves it and helps jog her memory. Thank you Plumwick Studio!</p>
    <div class="testi-rule"></div>
    <div class="testi-name">Marla T</div>
    <div class="testi-place">Fairview, MD</div>
  </div>
</section>

<section>
  <h2 class="section-title" style="top:3301px">WHY US?</h2>
  <div class="title-rule" style="top:3349px"></div>

  <div class="why-deco" style="left:145px" role="img" aria-label="Colorful paint splash behind icon"></div>
  <div class="why-circle" style="left:191px">
    <svg width="52" height="56" viewBox="0 0 52 56" fill="none" stroke="#e8542a" stroke-width="2.5"><rect x="3" y="14" width="16" height="38"/><rect x="25" y="14" width="24" height="16"/><rect x="25" y="36" width="24" height="16"/><circle cx="11" cy="5" r="3"/><path d="M8 24h6M8 32h6M8 40h6"/></svg>
  </div>
  <div class="why-title" style="left:98px">Your Idea Your Design</div>
  <p class="why-text" style="left:128px">Each art piece is customized for you! You choose your size, orientation and art style. Makes a perfect gift!!!</p>

  <div class="why-deco" style="left:496px" role="img" aria-label="Colorful paint splash behind icon"></div>
  <div class="why-circle" style="left:542px">
    <svg width="66" height="44" viewBox="0 0 66 44" fill="none" stroke="#e8542a" stroke-width="2.5"><path d="M14 6h30v26H14zM44 14h11l8 10v8H44z"/><circle cx="22" cy="36" r="5"/><circle cx="52" cy="36" r="5"/><path d="M2 14h9M4 20h7M6 26h5"/></svg>
  </div>
  <div class="why-title" style="left:449px">Fast Shipping</div>
  <p class="why-text" style="left:479px">Your artwork is printed and shipped in the USA! We offer fast turnaround with transit times typically 3-7 days. Free tracking with each order!!</p>

  <div class="why-deco" style="left:852px" role="img" aria-label="Colorful paint splash behind icon"></div>
  <div class="why-circle" style="left:898px">
    <svg width="50" height="62" viewBox="0 0 50 62" fill="none" stroke="#e8542a" stroke-width="2.5"><circle cx="25" cy="23" r="20"/><circle cx="25" cy="23" r="13"/><path d="M19 23l5 5 8-9M13 39l-7 18 8-3 4 7 6-14M37 39l7 18-8-3-4 7-6-14"/></svg>
  </div>
  <div class="why-title" style="left:805px">High Quality</div>
  <p class="why-text" style="left:835px">We’ve put a lot of effort ensuring your artwork is of the highest quality. Each piece is printed on the highest quality, gallery grade canvas. It is ready to hang upon arrival.!</p>
</section>

<footer>
  <div class="abs footer"></div>
  <div class="brand footer-brand"><span class="brand-dot"></span>Plumwick Studio</div>
  <svg class="abs" style="left:667px;top:3771px" width="26" height="18" viewBox="0 0 26 18" fill="none" stroke="#fff" stroke-width="1.6"><rect x="1" y="1" width="24" height="16"/><path d="M1 1l12 9 12-9"/></svg>
  <div class="abs footer-email">Email Us<br>info@plumwickstudio.com</div>
  <div class="abs follow">Follow us</div>
  <div class="social" style="left:945px;background:#3b5da8"></div>
  <div class="social" style="left:978px;background:#3f6fb5"></div>
  <div class="social" style="left:1010px;background:#444"></div>
  <div class="social" style="left:1043px;background:#d0202a"></div>
  <div class="footer-links">
    <span>About Us</span><span class="sep">|</span><span>My Orders</span><span class="sep">|</span><span>Testimonials</span><span class="sep">|</span><span>Get Started</span><span class="sep">|</span><span>FAQs</span><span class="sep">|</span><span>Privacy Policy</span><span class="sep">|</span><span>Terms and Conditions</span>
  </div>
  <div class="abs footer-rule"></div>
  <div class="abs copyright">Copyright © 2023 All Rights Reserved</div>
</footer>

</body>
</html>
```